HUMMING BENEATH LANTERNS - ONE LIVED TALE

A5 size book of 190 - 210 (70 or 80 gsm wood free paper). The concept revolves around an unseen being that stands on a lotus flower who enters an Indian temple with many of his devotees. Traditional design with photography of a colourful Indian temple is preferred though alternative idea would also be considered. Short narratives at the back of book would give prospective readers an instantaneous insight into the story.

```html
<!DOCTYPE html>
<html lang="en">
<head>
<meta charset="utf-8">
<title>Humming Beneath Lanterns – One Lived Tale</title>
<link rel="stylesheet" href="https://fonts.googleapis.com/css2?family=Dancing+Script:wght@400&family=Roboto+Condensed:wght@400&family=Roboto:wght@500&display=swap">
<style>
  :root {
    --stone-dark: #141626;
    --stone-navy: #262c4f;
    --dusk-violet: #6c5384;
    --temple-amber: #e38a2e;
    --glow-gold: #f6b64a;
    --light-core: #fde3a0;
    --text-white: #ffffff;
    --author-orange: #f29a22;
  }
  * { margin: 0; padding: 0; box-sizing: border-box; }
  html, body {
    width: 1086px;
    height: 1200px;
    overflow: hidden;
    background: var(--stone-dark);
  }
  .cover {
    position: relative;
    width: 1086px;
    height: 1200px;
    overflow: hidden;
  }
  .cover-art {
    position: absolute;
    inset: 0;
    background:
      linear-gradient(to bottom, rgba(20,22,38,0) 0%, rgba(20,22,38,0) 72%, rgba(20,22,38,0.85) 88%, var(--stone-dark) 100%),
      radial-gradient(ellipse 200px 260px at 50% 62%, var(--light-core) 0%, var(--glow-gold) 35%, rgba(227,138,46,0) 100%),
      radial-gradient(ellipse 330px 480px at 50% 50%, var(--temple-amber) 0%, var(--dusk-violet) 65%, rgba(108,83,132,0) 100%),
      radial-gradient(ellipse 620px 720px at 50% 45%, var(--stone-navy) 0%, #3a3f63 40%, var(--stone-dark) 100%);
  }
  .cover-text {
    position: absolute;
    left: 0;
    right: 0;
    text-align: center;
    color: var(--text-white);
  }
  .tagline {
    top: 953px;
    font-family: "Roboto Condensed", sans-serif;
    font-size: 25px;
    letter-spacing: 0.2px;
  }
  .title {
    top: 992px;
    font-family: "Dancing Script", cursive;
    font-weight: 400;
    font-size: 70px;
    line-height: 1.1;
    text-shadow: 0 2px 6px rgba(0,0,0,0.5);
  }
  .author {
    top: 1105px;
    font-family: "Roboto", sans-serif;
    font-weight: 500;
    font-size: 30px;
    letter-spacing: 3px;
    color: var(--author-orange);
  }
</style>
</head>
<body>
  <main class="cover">
    <div class="cover-art" role="img" aria-label="Photographic scene: a silhouetted robed figure standing on a pink lotus flower, seen through a weathered stone archway, facing a domed Indian temple glowing gold under sunlit tree branches, with fallen petals on the ground"></div>
    <p class="cover-text tagline">One Lived Tale</p>
    <h1 class="cover-text title">Humming Beneath Lanterns</h1>
    <p class="cover-text author">TERNWALE</p>
  </main>
</body>
</html>
```